Still Point website development

Need a website designed for a coaching business. Very high-end, luxury, professionalism, in the area of STRESS, see brief attached. I have a logo already
Updates

Slow in providing feedback

Target Market(s)

CEOs very successful men and wealthy females, high end luxury market

Industry/Entity Type

coaching

Number of Pages Required

1 page

Requirements
Must have
• Luxury look, professional, serious but warm, appealing to both sexes

```html
<!DOCTYPE html>
<html lang="en">
<head>
<meta charset="utf-8">
<title>Still Point — Lifestyle Coaching</title>
<link href="https://fonts.googleapis.com/css2?family=Montserrat:wght@400;500;600&family=Noto+Serif:wght@400;700&family=Nunito+Sans:wght@400&display=swap" rel="stylesheet">
<style>
:root{
  --ink:#151317;
  --black:#0c0a0c;
  --white:#ffffff;
  --text:#3a3a3a;
  --panel:#f4f3f2;
  --chip:#8a8a8a;
}
*{margin:0;padding:0;box-sizing:border-box}
html,body{width:1200px;height:2281px;overflow:hidden;background:var(--white)}
body{position:relative;font-family:"Montserrat",sans-serif;color:var(--text)}
.abs{position:absolute}

/* top bar */
.topbar{left:0;top:0;width:1200px;height:36px;background:var(--ink)}
.social-top{top:7px;display:flex;gap:7px;left:555px}
.chip{width:23px;height:23px;border-radius:50%;background:var(--chip)}
.contact{top:0;height:36px;display:flex;align-items:center;gap:8px;color:#e6e6e6;font-family:"Noto Serif",serif;font-size:13px}
.contact.phone{left:712px}
.contact.mail{left:898px}
.divider{top:10px;width:1px;height:16px;background:#444}

/* nav */
.navbar{left:0;top:36px;width:1200px;height:54px;background:var(--white)}
.brand-tab{left:46px;top:9px;width:312px;height:96px}
.brand-name{left:104px;top:38px;display:flex;align-items:center;gap:12px;font-family:"Noto Serif",serif;font-weight:700;font-size:23px;letter-spacing:3px;color:var(--ink)}
.brand-mark{width:18px;height:18px;background:var(--ink)}
.nav{top:52px;font-family:"Noto Serif",serif;font-size:15px;color:#555}
.nav a{position:absolute;white-space:nowrap;color:inherit;text-decoration:none}
.nav a.active{color:var(--ink)}
.nav-underline{left:575px;top:87px;width:40px;height:2px;background:var(--ink)}

/* hero */
.hero{left:0;top:90px;width:1200px;height:596px;
  background:
    radial-gradient(ellipse 160px 120px at 8% 12%,rgba(62,84,44,.85),transparent 70%),
    radial-gradient(ellipse 200px 150px at 88% 10%,rgba(70,92,50,.8),transparent 70%),
    radial-gradient(ellipse 140px 170px at 60% 50%,rgba(58,100,40,.85),transparent 70%),
    radial-gradient(ellipse 120px 110px at 52% 70%,rgba(226,222,214,.95),transparent 70%),
    radial-gradient(ellipse 260px 120px at 35% 42%,rgba(238,234,228,.85),transparent 70%),
    radial-gradient(ellipse 240px 160px at 92% 68%,rgba(214,210,204,.9),transparent 70%),
    radial-gradient(ellipse 220px 120px at 85% 42%,rgba(120,76,52,.85),transparent 70%),
    radial-gradient(ellipse 230px 170px at 14% 55%,rgba(168,112,76,.85),transparent 70%),
    radial-gradient(ellipse 420px 90px at 35% 96%,rgba(70,44,28,.9),transparent 75%),
    linear-gradient(100deg,#5b3a25 0%,#a8693c 30%,#c8894f 50%,#9a6a48 75%,#6a4a36 100%)}
.hero-shade{left:0;top:90px;width:1200px;height:596px;background:linear-gradient(180deg,rgba(0,0,0,.3),rgba(0,0,0,0) 45%)}
.hero-title{left:0;top:135px;width:1200px;text-align:center;font-family:"Noto Serif",serif;font-weight:700;font-size:52px;letter-spacing:1px;color:var(--white)}
.hero-sub{left:380px;top:204px;width:440px;text-align:center;font-weight:600;font-size:16.5px;line-height:23px;color:var(--white)}
.btn{display:flex;align-items:center;justify-content:space-between;background:var(--ink);color:var(--white);font-weight:600;border-radius:3px;box-shadow:0 3px 6px rgba(0,0,0,.3)}
.btn .go{width:31px;height:31px;border-radius:50%;background:var(--white);display:flex;align-items:center;justify-content:center}
.hero-btn{left:516px;top:266px;width:168px;height:47px;padding:0 10px 0 17px;font-size:17px}
.arrow{width:44px;height:44px;border:1.5px solid var(--white);border-radius:50%;display:flex;align-items:center;justify-content:center}
.dots{left:563px;top:633px;display:flex;gap:9px;align-items:center}
.dot{width:11px;height:11px;border-radius:50%;background:var(--white)}
.dot.on{width:16px;height:16px;border:2px solid var(--white);background:transparent;display:flex;align-items:center;justify-content:center}
.dot.on::after{content:"";width:8px;height:8px;border-radius:50%;background:var(--white)}

/* about */
.about-brand{left:150px;top:795px;display:flex;align-items:center;gap:18px;font-family:"Noto Serif",serif;font-weight:700;font-size:40px;letter-spacing:6px;color:var(--ink)}
.about-brand .brand-mark{width:32px;height:32px}
.photo-a{left:111px;top:918px;width:515px;height:374px;border-radius:4px;
  background:
    radial-gradient(ellipse 150px 110px at 78% 30%,rgba(246,236,204,.9),transparent 70%),
    radial-gradient(ellipse 340px 60px at 40% 67%,rgba(120,128,130,.55),transparent 75%),
    radial-gradient(ellipse 300px 110px at 45% 92%,rgba(92,90,78,.9),transparent 70%),
    radial-gradient(ellipse 120px 80px at 15% 80%,rgba(110,112,92,.7),transparent 70%),
    linear-gradient(180deg,#e7e4da 0%,#dcd6c2 35%,#a9a89c 58%,#8b8676 75%,#6b6656 100%)}
.photo-cut{left:547px;top:1124px;width:90px;height:180px;background:var(--white)}
.photo-b{left:555px;top:1134px;width:533px;height:158px;
  background:
    radial-gradient(ellipse 260px 40px at 30% 52%,rgba(170,176,190,.7),transparent 75%),
    radial-gradient(ellipse 300px 45px at 75% 68%,rgba(130,138,156,.75),transparent 75%),
    radial-gradient(ellipse 360px 50px at 40% 90%,rgba(96,104,124,.85),transparent 75%),
    linear-gradient(180deg,#f4f5f7 0%,#e6e8ee 35%,#b9bfcc 65%,#818a9e 100%)}
.about-h{left:647px;top:764px;font-family:"Noto Serif",serif;font-weight:700;font-size:33px;letter-spacing:1px;color:var(--ink)}
.about-sub{left:647px;top:813px;font-family:"Noto Serif",serif;font-size:23.5px;color:#333;letter-spacing:.3px}
.about-p{left:647px;top:859px;width:417px;font-family:"Nunito Sans",sans-serif;font-size:12.8px;line-height:22.2px;text-align:justify;color:#444}
.learn-btn{left:647px;top:1050px;width:168px;height:47px;padding:0 10px 0 18px;font-size:17px}

/* benefits */
.benefits{left:0;top:1380px;width:1200px;height:531px;background:var(--panel)}
.benefits-photo{left:440px;top:1380px;width:760px;height:531px;
  background:
    radial-gradient(ellipse 150px 200px at 88% 42%,rgba(236,232,226,.9),transparent 70%),
    radial-gradient(ellipse 130px 180px at 62% 48%,rgba(150,120,110,.55),transparent 70%),
    radial-gradient(ellipse 160px 120px at 82% 78%,rgba(40,36,38,.55),transparent 70%),
    radial-gradient(ellipse 260px 70px at 60% 90%,rgba(130,112,96,.6),transparent 75%),
    radial-gradient(ellipse 120px 160px at 45% 55%,rgba(160,140,132,.45),transparent 70%),
    linear-gradient(90deg,var(--panel) 0%,rgba(244,243,242,0) 28%),
    linear-gradient(180deg,#e6d8c8 0%,#d8c3ae 45%,#c4ab94 80%,#a89078 100%)}
.ben-h{left:111px;top:1455px;font-family:"Noto Serif",serif;font-weight:700;font-size:33px;letter-spacing:1px;color:var(--ink)}
.ben-rule{left:111px;top:1504px;width:111px;height:2px;background:var(--ink)}
.ben-list{left:111px;top:1520px;width:406px;list-style:none;font-family:"Nunito Sans",sans-serif;font-size:13px;line-height:20.6px;color:#444}
.ben-list li{position:relative;padding-left:14px;margin-bottom:11px;text-align:justify}
.ben-list li::before{content:"";position:absolute;left:0;top:6px;width:8px;height:8px;border:1.4px solid var(--ink);border-radius:50%}

/* footer */
.footer{left:0;top:1911px;width:1200px;height:370px;background:var(--black);border-radius:8px 8px 0 0}
.foot-brand{left:0;top:2003px;width:1200px;display:flex;justify-content:center;align-items:center;gap:14px;font-family:"Noto Serif",serif;font-weight:700;font-size:36px;letter-spacing:5px;color:var(--white)}
.foot-brand .brand-mark{width:26px;height:26px;background:var(--white)}
.foot-nav{left:0;top:2112px;width:1200px;display:flex;justify-content:center;gap:20px;font-family:"Noto Serif",serif;font-size:16.5px;color:var(--white);letter-spacing:.5px}
.foot-nav .sep{color:#999;font-size:12px;align-self:center}
.copy{left:0;top:2167px;width:1200px;text-align:center;font-family:"Noto Serif",serif;font-weight:700;font-size:12.5px;color:var(--white)}
.copy a{color:#aaa;font-weight:400;text-decoration:underline}
.social-foot{left:521px;top:2213px;display:flex;gap:9px}
.social-foot .chip{width:33px;height:33px}
.to-top{left:1105px;top:2166px;width:44px;height:44px;border-radius:50%;background:var(--white);display:flex;align-items:center;justify-content:center}
</style>
</head>
<body>

<!-- top bar -->
<div class="abs topbar"></div>
<div class="abs social-top"><span class="chip"></span><span class="chip"></span><span class="chip"></span><span class="chip"></span></div>
<div class="abs divider" style="left:693px"></div>
<div class="abs contact phone">
  <svg width="13" height="13" viewBox="0 0 24 24"><path fill="#e6e6e6" d="M6.6 10.8a15 15 0 0 0 6.6 6.6l2.2-2.2c.3-.3.7-.4 1-.2 1.1.4 2.3.6 3.6.6.6 0 1 .4 1 1V20c0 .6-.4 1-1 1A17 17 0 0 1 3 4c0-.6.4-1 1-1h3.5c.6 0 1 .4 1 1 0 1.3.2 2.5.6 3.6.1.3 0 .7-.2 1z"/></svg>
  Tel: +1 (555) 010 2468
</div>
<div class="abs divider" style="left:875px"></div>
<div class="abs contact mail">
  <svg width="15" height="11" viewBox="0 0 15 11"><rect width="15" height="11" fill="#e6e6e6"/><path d="M0 0l7.5 6L15 0" fill="none" stroke="#151317" stroke-width="1.3"/></svg>
  Mail: hello@stillpoint.example
</div>

<!-- navigation -->
<div class="abs navbar"></div>
<svg class="abs brand-tab" viewBox="0 0 312 96"><polygon points="25,0 287,0 312,27 312,40 0,40 0,27" fill="#fff"/><polygon points="0,27 312,27 287,62 60,62 62,96 40,80 25,62" fill="#fff"/></svg>
<div class="abs brand-name"><span class="brand-mark"></span>STILL POINT</div>
<nav class="abs nav" style="left:0">
  <a class="active" style="left:575px">Home</a>
  <a style="left:649px">Our Services</a>
  <a style="left:765px">About Us</a>
  <a style="left:858px">Our Team</a>
  <a style="left:956px">Blog</a>
  <a style="left:1018px">Contact Us</a>
</nav>
<div class="abs nav-underline"></div>

<!-- hero -->
<div class="abs hero" role="img" aria-label="Spa scene with aromatherapy oils, candles, a plant and a client relaxing on a massage table"></div>
<div class="abs hero-shade"></div>
<h1 class="abs hero-title">STILL POINT</h1>
<p class="abs hero-sub">Sedut slseopse erseo seisej lsskseioiesp seosiciatis uksnsdeom nisiste natus.</p>
<div class="abs btn hero-btn">Get Started
  <span class="go"><svg width="13" height="10" viewBox="0 0 13 10"><path d="M1 5h10M7 1l4 4-4 4" fill="none" stroke="#151317" stroke-width="1.4"/></svg></span>
</div>
<div class="abs arrow" style="left:35px;top:378px"><svg width="22" height="16" viewBox="0 0 22 16"><path d="M21 8H2M9 1L2 8l7 7" fill="none" stroke="#fff" stroke-width="2"/></svg></div>
<div class="abs arrow" style="left:1121px;top:378px"><svg width="22" height="16" viewBox="0 0 22 16"><path d="M1 8h19M13 1l7 7-7 7" fill="none" stroke="#fff" stroke-width="2"/></svg></div>
<div class="abs dots"><span class="dot"></span><span class="dot"></span><span class="dot"></span><span class="dot on"></span></div>

<!-- about -->
<div class="abs about-brand"><span class="brand-mark"></span>STILL POINT</div>
<div class="abs photo-a" role="img" aria-label="Woman sitting cross-legged on a mountain rock with arms spread wide"></div>
<div class="abs photo-cut"></div>
<div class="abs photo-b" role="img" aria-label="Woman with open arms in front of misty mountain ranges"></div>
<h2 class="abs about-h">ABOUT STILL POINT</h2>
<p class="abs about-sub">Still Point came about due to my desire</p>
<p class="abs about-p">to help people lead a better and healthier life. Initially, I was involved in the fitness/body side of health. As years passed and my experience grew, I realized how important the mind was in total wellness, and that the mind is all powerful and controlling. Control the mind, control the body and achieve success. Stress can be the most debilating factor in our lives, it is the root cause of so many diseases and costs the US workplace an estimated 300 billion dollars due to loss of productivity.</p>
<div class="abs btn learn-btn">Learn More
  <span class="go"><svg width="13" height="10" viewBox="0 0 13 10"><path d="M1 5h10M7 1l4 4-4 4" fill="none" stroke="#3a7a4a" stroke-width="1.4"/></svg></span>
</div>

<!-- benefits -->
<div class="abs benefits"></div>
<div class="abs benefits-photo" role="img" aria-label="Group of women meditating cross-legged in a row in a bright yoga studio"></div>
<h2 class="abs ben-h">BENEFITS</h2>
<div class="abs ben-rule"></div>
<ul class="abs ben-list">
  <li>Experience</li>
  <li>Sector expert Health/Wellness. Presented at numerous industry shows and quoted in national publications (not as a coach, I'm new, but in the health &amp; wellness space)</li>
  <li>Excellent listener...being in sales for many years, the secret is to really listen...and get to the end game, and make it feel as if it was their decision. Not sure how to word this as a benefit.</li>
  <li>Access/resources industry professionals, sport psychologist...just spent a few hours with the Mind performance coach for a major league baseball team... I can get the best advice &amp; latest techniques in mind/body training performance.</li>
  <li>Private, more than happy to sign confidentiality agreement. Especially for the business man.</li>
</ul>

<!-- footer -->
<footer class="abs footer"></footer>
<div class="abs foot-brand"><span class="brand-mark"></span>STILL POINT</div>
<div class="abs foot-nav">
  <span>Home</span><span class="sep">|</span><span>Our Services</span><span class="sep">|</span><span>About Us</span><span class="sep">|</span><span>Our Team</span><span class="sep">|</span><span>Blog</span><span class="sep">|</span><span>Contact Us</span>
</div>
<p class="abs copy">Copyright © 2022 <a>stillpoint</a> | All Rights Reserved | Terms &amp; Conditions | Privacy Policy</p>
<div class="abs social-foot"><span class="chip"></span><span class="chip"></span><span class="chip"></span><span class="chip"></span></div>
<div class="abs to-top"><svg width="12" height="8" viewBox="0 0 12 8"><path d="M1 7l5-5 5 5" fill="none" stroke="#151317" stroke-width="1.8"/></svg></div>

</body>
</html>
```